Letterhead Design Project

Letterhead for a Consultant Cardiologist in Adelaide Australia. Should be very classy, mature and imposing. I would prefer colours that portray confidence, gentleness and serenity.

The PDF attached is for you to see the details that will be on the letterhead and not the design which is extremely poor!

Target Market(s)

Health professionals especially medical doctors

Industry/Entity Type

Consultant

```html
<!DOCTYPE html>
<html lang="en">
<head>
<meta charset="utf-8">
<title>Letterhead – Dr Adaeze K. Morland, Cardiologist</title>
<link rel="stylesheet" href="https://fonts.googleapis.com/css2?family=Open+Sans:ital,wght@0,400;0,600;0,700;0,800;1,700&display=swap">
<style>
  :root {
    --page: #ffffff;
    --band-light: #f2f2f2;
    --band-mid: #d4d4d4;
    --band-dark: #9c9c9c;
    --accent-red: #d21f1f;
    --label-orange: #d9531e;
    --text-white: #ffffff;
    --text-grey: #6e6e6e;
    --text-dark: #3a3a3a;
  }
  * { margin: 0; padding: 0; box-sizing: border-box; }
  html, body { width: 849px; height: 1200px; overflow: hidden; background: var(--page); }
  body { font-family: "Open Sans", Arial, sans-serif; }

  .letterhead { position: relative; width: 849px; height: 1200px; background: var(--page); }

  .header-band {
    position: absolute; left: 0; top: 0; width: 849px; height: 140px;
    background: linear-gradient(180deg, var(--band-dark) 0%, var(--band-mid) 45%, var(--band-light) 100%);
  }
  .header-rule {
    position: absolute; left: 0; top: 140px; width: 849px; height: 6px;
    background: var(--accent-red);
  }
  .brand-dot {
    position: absolute; left: 40px; top: 26px; width: 88px; height: 88px;
    border-radius: 50%; background: var(--accent-red);
  }
  .doctor-name {
    position: absolute; left: 160px; top: 14px;
    font-size: 25px; font-weight: 800; color: var(--text-white); letter-spacing: 0.3px;
  }
  .credentials {
    position: absolute; left: 162px; top: 50px;
    font-size: 12px; font-weight: 600; color: var(--text-white); letter-spacing: 1px;
  }
  .specialty {
    position: absolute; left: 162px; top: 68px;
    font-size: 17px; font-weight: 700; font-style: italic; color: var(--accent-red);
  }

  .footer { position: absolute; left: 0; top: 1068px; width: 849px; height: 120px; }
  .practice { position: absolute; top: 0; font-size: 11px; line-height: 14.5px; color: var(--text-grey); }
  .practice .label { color: var(--label-orange); font-weight: 600; }
  .practice .site { color: var(--label-orange); font-weight: 600; }
  .practice-linden { left: 93px; width: 170px; }
  .practice-northgate { left: 268px; width: 300px; }
  .practice-bayside { left: 622px; width: 200px; }
  .inline-provider { margin-left: 14px; color: var(--text-dark); }
</style>
</head>
<body>
<main class="letterhead">
  <header>
    <div class="header-band" role="img" aria-label="Soft grey gradient header band with a faint textured pattern"></div>
    <div class="header-rule"></div>
    <div class="brand-dot"></div>
    <h1 class="doctor-name">Dr Adaeze K. Morland</h1>
    <p class="credentials">M.B.B.S, F.M.C.P, F.R.A.C.P</p>
    <p class="specialty">Cardiologist</p>
  </header>

  <footer class="footer">
    <address class="practice practice-linden">
      <span class="label">Consulting</span><br>
      <span class="site">The Linden Specialist Centre</span><br>
      48 Carrow Road<br>
      Carrow Park SA 5019<br>
      T: 8190 3342<br>
      F: 8190 3355
    </address>
    <address class="practice practice-northgate">
      <span class="label">Provider No: 518822QA</span><br>
      <span class="site">Northgate Heart Clinic</span><br>
      6 Specialist Clinic, Harbourview Private Hospital<br>
      14-20 Mallee Street, Grange Vale SA 5120<br>
      T: 8277 6104 &nbsp; F: 8277 6190<br>
      E: clinic@northgateheart.au<span class="inline-provider">Provider No: 518822QB</span>
    </address>
    <address class="practice practice-bayside">
      <span class="label">Bayside Regional Hospital</span><br>
      9 Harbour Lane<br>
      Bayside 5710<br>
      T: 8631 4400<br>
      F: 8190 3355<br>
      Provider No: 518822QC
    </address>
  </footer>
</main>
</body>
</html>
```